Corvane Holdings , new business card design

investment firm with corporate clients . need double sided business card , vertical and horizontal options ,logo must be clear. prefer pantone colors only and sharp design. website also www.corvane.ae

Khalid Bin Tarrafi
Managing Director
Tel. +971 4 387 2940
Mobile +971 50 518 2403
khalid@corvane.ae
Q-Span Plaza, officw 18-B07, Warqa Gardens, Dubai

Contact Information for Business Card

Khalid Bin Tarrafi
Managing Director

Font styles to use
Serif

Colors

Designer to choose colors to be used in the design.

```html
<!DOCTYPE html>
<html lang="en">
<head>
<meta charset="UTF-8">
<title>Corvane Holdings – Business Card</title>
<link rel="stylesheet" href="https://fonts.googleapis.com/css2?family=Lato:wght@400;700&family=Montserrat:wght@500;700&display=swap">
<style>
  :root {
    --backdrop: #e7e8ea;
    --card: #ffffff;
    --navy: #1d2f6b;
    --steel: #4a7196;
    --ink: #1f1f1f;
    --muted: #333a44;
  }
  * { box-sizing: border-box; margin: 0; padding: 0; }
  html, body { width: 1200px; height: 960px; overflow: hidden; }
  body {
    background: var(--backdrop);
    font-family: "Lato", Arial, sans-serif;
    color: var(--ink);
    position: relative;
  }
  .card {
    position: absolute;
    left: 290px;
    width: 620px;
    height: 354px;
    background: var(--card);
    box-shadow: 0 8px 24px rgba(0,0,0,0.14);
    overflow: hidden;
  }
  .card--front { top: 60px; }
  .card--back { top: 520px; }

  .wordmark {
    font-family: "Lato", Arial, sans-serif;
    font-weight: 400;
    color: var(--ink);
    text-transform: uppercase;
    letter-spacing: 0.28em;
    white-space: nowrap;
  }

  /* front */
  .front-brand {
    position: absolute;
    top: 118px;
    left: 0;
    width: 100%;
    text-align: center;
    font-size: 36px;
  }
  .front-url {
    position: absolute;
    top: 200px;
    left: 0;
    width: 100%;
    text-align: center;
    font-size: 19px;
    letter-spacing: 0.2em;
    color: var(--ink);
  }

  /* back */
  .back-brand {
    position: absolute;
    top: 46px;
    right: 34px;
    font-size: 22px;
  }
  .holder {
    position: absolute;
    top: 56px;
    left: 0;
    padding-left: 30px;
  }
  .holder__tab {
    position: absolute;
    left: -10px;
    top: 2px;
    width: 24px;
    height: 44px;
    background: var(--navy);
    border-radius: 12px;
  }
  .holder__name {
    font-family: "Montserrat", Arial, sans-serif;
    font-weight: 700;
    font-size: 15px;
    color: var(--navy);
    text-transform: uppercase;
    letter-spacing: 0.01em;
  }
  .holder__title {
    font-family: "Montserrat", Arial, sans-serif;
    font-weight: 500;
    font-size: 14px;
    color: var(--navy);
    text-transform: uppercase;
    margin-top: 6px;
    letter-spacing: 0.02em;
  }
  .contacts {
    position: absolute;
    left: 30px;
    top: 212px;
    list-style: none;
    font-size: 14px;
    color: var(--muted);
  }
  .contacts li {
    display: flex;
    align-items: flex-start;
    gap: 7px;
    line-height: 17px;
    margin-bottom: 5px;
  }
  .contacts svg { width: 12px; height: 12px; margin-top: 3px; flex: none; fill: var(--navy); }
  .contacts .address { margin-top: 3px; }
  .contacts .address svg { width: 12px; height: 14px; margin-top: 2px; }

  .url-tab {
    position: absolute;
    right: 22px;
    bottom: 38px;
    width: 262px;
    height: 42px;
    background: var(--steel);
    border-radius: 21px 21px 0 21px;
    color: #fff;
    font-size: 16px;
    letter-spacing: 0.2em;
    display: flex;
    align-items: center;
    justify-content: center;
  }
</style>
</head>
<body>

<section class="card card--front" aria-label="Card front">
  <div class="wordmark front-brand">Corvane Holdings</div>
  <div class="front-url">www.corvane.ae</div>
</section>

<section class="card card--back" aria-label="Card back">
  <div class="holder">
    <span class="holder__tab"></span>
    <p class="holder__name">Khalid Bin Tarrafi</p>
    <p class="holder__title">Managing Director</p>
  </div>

  <div class="wordmark back-brand">Corvane Holdings</div>

  <ul class="contacts">
    <li>
      <svg viewBox="0 0 24 24" aria-hidden="true"><path d="M6.6 10.8a15 15 0 0 0 6.6 6.6l2.2-2.2a1 1 0 0 1 1-.25 11.4 11.4 0 0 0 3.6.57 1 1 0 0 1 1 1V20a1 1 0 0 1-1 1A17 17 0 0 1 3 4a1 1 0 0 1 1-1h3.5a1 1 0 0 1 1 1c0 1.25.2 2.45.57 3.57a1 1 0 0 1-.25 1z"/></svg>
      <span>+971 4 387 2940</span>
    </li>
    <li>
      <svg viewBox="0 0 24 24" aria-hidden="true"><path d="M7 1h10a2 2 0 0 1 2 2v18a2 2 0 0 1-2 2H7a2 2 0 0 1-2-2V3a2 2 0 0 1 2-2zm0 3v13h10V4zm5 15a1.2 1.2 0 1 0 0 2.4 1.2 1.2 0 0 0 0-2.4z"/></svg>
      <span>+971 50 518 2403</span>
    </li>
    <li>
      <svg viewBox="0 0 24 24" aria-hidden="true"><path d="M2 6a2 2 0 0 1 2-2h16a2 2 0 0 1 2 2v12a2 2 0 0 1-2 2H4a2 2 0 0 1-2-2zm2 .5V7l8 5 8-5v-.5z"/></svg>
      <span>khalid@corvane.ae</span>
    </li>
    <li class="address">
      <svg viewBox="0 0 20 24" aria-hidden="true"><path d="M10 0a8 8 0 0 1 8 8c0 6-8 16-8 16S2 14 2 8a8 8 0 0 1 8-8zm0 4.5a3.5 3.5 0 1 0 0 7 3.5 3.5 0 0 0 0-7z"/></svg>
      <span>Q-Span Plaza, officw 18-B07<br>Warqa Gardens, Dubai</span>
    </li>
  </ul>

  <div class="url-tab">www.corvane.ae</div>
</section>

</body>
</html>
```